Stationery Design Project for Nimbora, Chicago

Nimbora, a street parking application which helps car drivers find a street parking spot by offering an ideal path along which to look for parking. This path is calculated by our algorithm based on data (e.g. historical data, baseball games schedule, etc.). Along this path the driver will find a spot and will also save 70% of the search time. Customer we target is reg. between 21 and 45 yo.

We envision something young, fresh, bright and original. Slightly abstract maybe. It should represent the idea and elements of finding street parking in the city, e.g. car(s), parking spot, people, city, etc. (just ideas!).

Logo is attached.

Requirement:
- Business Cards (2 Sided Full Color CMYK)
- Letterhead (1 Sided Full Color CMYK)
- Envelope (1 Sided Full Color CMYK)
- Sticker (1 Sided Full Color CMYK), round with a 2inch diameter.

Reason: We're starting to get more and more designs and need more time to look into all of them. Very exciting!! Thanks to everybody!

Hi all, we're in the process of selecting our favs. Though choices!!! Really good submissions. Will keep you posted and sorry for the delay.

Target Market(s)

Car drivers and owners between 21 and 45

Industry/Entity Type

Parking

Requirements
Must have
• Sticker should be round and include company URL nimbora.com and the new logo which we will attach soon.
Should not have
• Should not be too serious or boring.

```html
<!DOCTYPE html>
<html lang="en">
<head>
<meta charset="utf-8">
<title>Nimbora Letterhead</title>
<link href="https://fonts.googleapis.com/css2?family=Open+Sans:wght@300;600&display=swap" rel="stylesheet">
<style>
  :root {
    --canvas: #ffffff;
    --page-edge: #222222;
    --ink: #3a3a3a;
    --ink-soft: #4a4a4a;
    --brand-blue: #1b7cc0;
    --divider-grey: #bbbbbb;
    --divider-blue: #8cc8ea;
    --skyline-tint: #fdf1dd;
    --skyline-tint-soft: #fef7ec;
  }
  html, body {
    margin: 0;
    padding: 0;
    width: 902px;
    height: 1200px;
    overflow: hidden;
    background: var(--canvas);
  }
  .canvas {
    position: relative;
    width: 902px;
    height: 1200px;
    background: var(--canvas);
  }
  .letterhead {
    position: absolute;
    left: 59px;
    top: 77px;
    width: 783px;
    height: 1028px;
    border: 1px solid var(--page-edge);
    box-sizing: border-box;
    overflow: hidden;
    background: var(--canvas);
  }
  .brand {
    position: absolute;
    left: 42px;
    top: 45px;
    display: flex;
    align-items: center;
    gap: 9px;
  }
  .brand-dot {
    width: 64px;
    height: 64px;
    border-radius: 50%;
    background: var(--brand-blue);
  }
  .brand-name {
    font-family: "Open Sans", sans-serif;
    font-weight: 600;
    font-size: 34px;
    line-height: 1;
    color: var(--ink);
  }
  .contact-line {
    position: absolute;
    right: 43px;
    top: 75px;
    margin: 0;
    font-family: "Open Sans", sans-serif;
    font-weight: 300;
    font-size: 10px;
    line-height: 1;
    color: var(--ink-soft);
    white-space: nowrap;
  }
  .contact-line .sep {
    color: var(--divider-grey);
    margin: 0 11px;
  }
  .contact-line .sep-accent {
    color: var(--divider-blue);
  }
  .skyline-art {
    position: absolute;
    left: 0;
    bottom: 0;
    width: 783px;
    height: 523px;
  }
</style>
</head>
<body>
  <div class="canvas">
    <div class="letterhead">
      <div class="brand">
        <div class="brand-dot"></div>
        <span class="brand-name">Nimbora</span>
      </div>
      <p class="contact-line">5678 Elm Avenue, Suite B<span class="sep">|</span>Oakdale, IL 54321<span class="sep sep-accent">|</span>www.nimbora.com</p>
      <svg class="skyline-art" viewBox="0 0 783 523" role="img" aria-label="Faint city skyline of tall buildings framed by a large circle">
        <defs>
          <radialGradient id="skylineGlow" cx="50%" cy="60%" r="60%">
            <stop offset="0%" stop-color="var(--skyline-tint-soft)"/>
            <stop offset="100%" stop-color="var(--skyline-tint)"/>
          </radialGradient>
        </defs>
        <circle cx="386" cy="373" r="371" fill="url(#skylineGlow)"/>
      </svg>
    </div>
  </div>
</body>
</html>
```